One Pager Fact Sheet Design

I need a couple of headers and footer designed to use for information security fact sheets to give to customers. Similar to the one listed below.

```html
<!DOCTYPE html>
<html lang="en">
<head>
<meta charset="utf-8">
<title>Fact Sheet Headers and Footer</title>
<link rel="stylesheet" href="https://fonts.googleapis.com/css2?family=PT+Sans:wght@400;700&display=swap">
<style>
  :root {
    --backdrop: #232323;
    --brand-red: #e3232b;
    --deep-red: #b61d22;
    --mid-red: #d8262d;
    --glow-red: #f06a6e;
    --panel-grey: #b5b5b6;
    --paper: #f5f0f0;
    --ink: #1c1c1c;
    --white: #ffffff;
    --social: #4a4a4a;
  }
  * { box-sizing: border-box; margin: 0; padding: 0; }
  html, body {
    width: 1200px; height: 675px; overflow: hidden;
    background: var(--backdrop);
    font-family: "PT Sans", "Segoe UI", sans-serif;
  }
  .sheet {
    position: absolute; left: 40px; top: 18px;
    width: 1122px; height: 618px;
    background: var(--paper);
    border-top: 3px solid var(--brand-red);
    border-bottom: 3px solid var(--white);
  }
  .header { position: absolute; left: 0; width: 1122px; display: flex; }
  .header--cover { top: 0; height: 241px; }
  .header--page { top: 349px; height: 100px; }
  .brand-panel {
    width: 414px; height: 100%;
    background: var(--panel-grey);
    display: flex; align-items: center; justify-content: center; gap: 12px;
  }
  .header--page .brand-panel { width: 413px; }
  .brand-mark {
    width: 50px; height: 50px; border-radius: 50%;
    border: 7px solid var(--brand-red);
    flex: none;
  }
  .brand-name {
    font-weight: 700; font-size: 50px; color: var(--brand-red);
    letter-spacing: -0.5px; line-height: 1;
  }
  .title-band {
    position: relative; flex: 1; height: 100%;
    background:
      radial-gradient(ellipse 340px 120px at 200px 55%, rgba(240,106,110,0.55), transparent 70%),
      linear-gradient(90deg, var(--deep-red) 0%, var(--mid-red) 45%, var(--brand-red) 100%);
    display: flex; align-items: center; padding-left: 26px;
    overflow: hidden;
  }
  .header--page .title-band { padding-left: 27px; }
  .title {
    color: var(--white); font-size: 27px; font-weight: 400;
    position: relative; z-index: 1;
  }
  .title strong { font-weight: 700; }
  .security-art {
    position: absolute; right: 0; top: 0; width: 270px; height: 100%;
    background: radial-gradient(circle at 110px 50%, rgba(255,170,172,0.55) 0%, rgba(240,90,96,0.35) 35%, transparent 70%);
  }
  .header--page .security-art {
    background: radial-gradient(circle at 110px 50%, rgba(255,170,172,0.5) 0%, rgba(240,90,96,0.3) 30%, transparent 65%);
  }
  .footer {
    position: absolute; left: 0; top: 515px; width: 1122px; height: 97px;
    background: var(--panel-grey);
    border-top: 5px solid var(--brand-red);
    display: flex; align-items: center; padding-left: 35px;
    font-size: 15.5px; color: var(--ink);
  }
  .contact { display: flex; align-items: center; gap: 6px; margin-right: 14px; }
  .contact--phone { margin-left: 4px; }
  .contact-icon { width: 21px; height: 21px; flex: none; }
  .footer-divider {
    width: 3px; height: 28px; background: var(--brand-red);
    margin: 0 16px 0 2px;
  }
  .social-dots { display: flex; gap: 8px; margin-right: 10px; }
  .social-dot { width: 22px; height: 22px; border-radius: 50%; background: var(--social); }
</style>
</head>
<body>
  <main class="sheet">
    <section class="header header--cover">
      <div class="brand-panel">
        <span class="brand-mark"></span>
        <span class="brand-name">brightvault</span>
      </div>
      <div class="title-band">
        <h1 class="title"><strong>FACT SHEET</strong>: Information Security</h1>
        <div class="security-art" role="img" aria-label="Illustration of a glowing shield with keyhole surrounded by circuit rings and device icons above an open hand"></div>
      </div>
    </section>

    <section class="header header--page">
      <div class="brand-panel">
        <span class="brand-mark"></span>
        <span class="brand-name">brightvault</span>
      </div>
      <div class="title-band">
        <h2 class="title"><strong>FACT SHEET</strong>: Page 1</h2>
        <div class="security-art" role="img" aria-label="Illustration of a shield with keyhole inside circuit rings"></div>
      </div>
    </section>

    <footer class="footer">
      <div class="contact">
        <svg class="contact-icon" viewBox="0 0 22 22" aria-hidden="true">
          <circle cx="11" cy="11" r="11" fill="#e3232b"/>
          <circle cx="11" cy="11" r="6" fill="none" stroke="#fff" stroke-width="1.6"/>
          <ellipse cx="11" cy="11" rx="2.6" ry="6" fill="none" stroke="#fff" stroke-width="1.4"/>
          <line x1="5" y1="11" x2="17" y2="11" stroke="#fff" stroke-width="1.4"/>
        </svg>
        <span>brightvault.in&nbsp; brightvault.gov.org</span>
      </div>
      <div class="contact">
        <svg class="contact-icon" viewBox="0 0 22 22" aria-hidden="true">
          <circle cx="11" cy="11" r="11" fill="#e3232b"/>
          <path d="M7 6 L16 10 L12 11.5 L15 15 L13.5 16.3 L10.6 12.8 L8.6 16 Z" fill="#fff"/>
        </svg>
        <span>profiles.net/company/brightvault.gov.org</span>
      </div>
      <div class="contact contact--phone">
        <svg class="contact-icon" viewBox="0 0 22 22" aria-hidden="true">
          <circle cx="11" cy="11" r="11" fill="#e3232b"/>
          <path d="M5 9 Q11 4 17 9 L15.5 10.5 L13.5 9.5 L13.5 8.3 Q11 7.4 8.5 8.3 L8.5 9.5 L6.5 10.5 Z" fill="#fff"/>
          <rect x="7" y="11" width="8" height="5" rx="1" fill="#fff"/>
        </svg>
        <span>01632 960 418</span>
      </div>
      <span class="footer-divider"></span>
      <div class="social-dots" aria-hidden="true">
        <span class="social-dot"></span>
        <span class="social-dot"></span>
        <span class="social-dot"></span>
        <span class="social-dot"></span>
      </div>
      <span>@brightvault.gov.org</span>
    </footer>
  </main>
</body>
</html>
```